Create a wordpress website for Tovarin business solution

This project is to create a complete website with all pages.

Overview
The purpose of this project is to create a full complete website with all pages (16 pages). The site should be professional and modern. The site is for an IT recruiting and IT training company. The site needs to be easy to administer and update content. It should be simple to add pages, videos and testimonials later. I will leave the site layout, color schemes and flow to the designers.

Navigation Menu (Home, who we are, what we do, what makes us different, why it matters, candidate portal, contact us, Blog)

WHO WE ARE should be a drop down menu with link to pages (about us, mission, vision and purpose, our team)

WHAT WE DO should be drop down menu with link to the following pages (IT Recruiting, IT Training, Hardware and software sales)

What makes us different should be single page with different paragraph titles. (We live what we do, we don't compromise quality, we share knowledge, staffing guarantee)

Why it matters should be single page with paragraph titles. (Quickly fill positions, candidate career development)

Candidate portal should links to my portal login page. I can add the correct URL later. I just need it to link to somewhere. I can change it.

Contact us should have (address, phone number, google map and a form to submit request for a call back)

Blog - This link should launch a wordpress blogging module

Target Market(s)

IT RECRUITING AND CONSULTING

Industry/Entity Type

It Company

Coding

Coded - Design and coding required

Requirements
Must have
• Company Logo
• Navigation Menu (Home, who we are, what we do, what makes us different, why it matters, candidate portal, contact us)
• WHO WE ARE should be a drop down menu with link to pages (about us, mission, vision and purpose, our team)
• WHAT WE DO should be drop down menu with link to the following pages (IT Recruiting, IT Training, Hardware and software sales)
• What makes us different should be single page with different paragraph titles. (We live what we do, we don't compromise quality, we share knowledge, staffing guarantee)
• Why it matters should be single page with paragraph titles. (Quickly fill positions, candidate career development)
• Candidate portal should links to my portal login page. I can add the correct URL later. I just need it to link to somewhere. I can change it.
• Contact us should have (address, phone number, google map and a form to submit request for a call back)

```html
<!DOCTYPE html>
<html lang="en">
<head>
<meta charset="utf-8">
<title>Tovarin Business Solution</title>
<link href="https://fonts.googleapis.com/css2?family=Open+Sans:ital,wght@1,400&family=Roboto:wght@300;400;500;700&display=swap" rel="stylesheet">
<style>
:root{
  --orange:#f7a64a;
  --orange-deep:#e9801f;
  --orange-icon:#ea7a1c;
  --nav-text:#b4560f;
  --blue:#0f5ba8;
  --navy:#0d4f9a;
  --ink:#222;
  --muted:#666;
  --line:#d4d4d4;
  --band:#ececec;
}
*{margin:0;padding:0;box-sizing:border-box}
html,body{width:776px;height:1200px;overflow:hidden;background:#fff}
body{position:relative;font-family:'Roboto',sans-serif;color:var(--ink)}
.abs{position:absolute}

/* header */
.header-contact{top:12px;display:flex;align-items:center;gap:8px}
.header-contact .label{font-size:11.5px;color:#333;line-height:1.1}
.header-contact .value{font-size:14px;color:var(--blue);line-height:1.1}
.call{left:48px}
.talk{right:58px}
.brand{left:0;width:776px;top:4px;text-align:center}
.brand-name{font-size:38px;font-weight:500;color:var(--navy);letter-spacing:1px;line-height:1}
.brand-tag{font-size:8.5px;color:#666;letter-spacing:1.4px;margin-top:1px}
.brand-tag i{display:inline-block;width:4px;height:2px;background:var(--orange-icon);vertical-align:middle;margin:0 5px}

/* nav */
.main-nav{left:50px;top:54px;width:676px;height:40px;background:var(--orange);border-radius:6px;display:flex;align-items:center;justify-content:center;z-index:2}
.main-nav a{font-size:9.6px;font-weight:500;color:var(--nav-text);text-decoration:none;padding:0 9px;border-left:1px solid #fff3;line-height:14px}
.main-nav a:first-child{border-left:0;color:var(--blue)}
.main-nav a+a{border-left:1px solid #fbe1c2}

/* hero */
.hero{left:0;top:74px;width:776px;height:364px;background:linear-gradient(100deg,#d9dfe3 0%,#b9c4cc 35%,#8d9aa6 60%,#b7bdc2 80%,#9aa3ab 100%)}
.hero-title{left:52px;top:166px;font-family:'Open Sans',sans-serif;font-style:italic;font-size:52px;color:#fff;letter-spacing:-0.5px;text-shadow:0 1px 3px #0004}
.hero-sub{left:52px;top:226px;font-size:25px;font-weight:300;color:#fff;text-shadow:0 1px 3px #0004}
.hero-line{left:52px;top:264px;font-size:14.5px;color:#fff;line-height:17px;text-shadow:0 1px 2px #0005}
.btn-hero{top:318px;height:34px;display:flex;align-items:center;border-radius:2px;color:#fff;font-size:10.5px}
.btn-hero .ic{width:34px;height:34px;display:flex;align-items:center;justify-content:center;border-right:1px solid #fff5}
.btn-hero .tx{padding:0 11px}
.quote{left:50px;width:114px;background:var(--orange-icon)}
.more{left:171px;width:114px;background:var(--orange)}

/* welcome */
.welcome-title{left:0;width:776px;top:462px;text-align:center;font-size:29px;font-weight:300;color:#111}
.welcome-title span{color:var(--blue);font-weight:400}
.welcome-text{left:80px;width:616px;top:511px;text-align:center;font-size:9.4px;line-height:14.8px;color:#555}
.welcome-text b{color:#333}

/* services */
.service{top:586px;width:216px;height:243px;border:1px solid var(--line);text-align:center}
.service .icon{width:78px;height:78px;border-radius:50%;background:var(--orange-icon);margin:20px auto 0;display:flex;align-items:center;justify-content:center}
.service h3{font-size:16px;font-weight:400;color:var(--blue);margin-top:16px}
.service p{font-size:9px;line-height:14.8px;color:#666;margin:7px 18px 0}
.service .read{display:inline-block;margin-top:8px;width:94px;height:34px;line-height:34px;background:var(--orange);color:#fff;font-size:10px;font-weight:500}

/* partners */
.partners{left:50px;top:856px;width:676px;height:101px;background:var(--band);box-shadow:0 10px 14px -8px #0003}
.partners-label{left:50px;top:856px}
.partners-label .txt{left:12px;top:20px;font-size:21px;font-weight:300;color:#fff;line-height:27px}
.badge{top:876px;height:60px;border-radius:3px}

/* footer */
.footer{left:0;top:990px;width:776px;height:170px;background:var(--orange);border-top:3px solid var(--orange-deep)}
.f-head{top:1018px;font-size:12.5px;color:var(--blue)}
.f-row{display:flex;gap:8px;font-size:9.2px;line-height:15px;color:#5b3b1a}
.news{display:flex;gap:6px;font-size:9.2px;line-height:14px;color:#6b3e10}
.news .thumb{width:36px;height:36px;border-radius:50%;flex:none}
.news small{display:block;font-size:8px;color:#222;line-height:11px}
.arrow-box{top:1019px;width:14px;height:14px;border:1px solid #8a4b12;display:flex;align-items:center;justify-content:center}
.foot-brand{left:592px;top:1034px;width:110px;text-align:center;color:#fff}
.foot-brand .n{font-size:24px;font-weight:500;line-height:1}
.foot-brand .t{font-size:6px;letter-spacing:1px}
.social{top:1076px;width:28px;height:28px;border-radius:50%}
.copyright{left:0;top:1160px;width:776px;height:40px;background:var(--orange-deep);text-align:center;line-height:40px;font-size:9.5px;color:#fff;font-weight:500}
</style>
</head>
<body>

<header>
  <div class="abs header-contact call">
    <svg width="14" height="28" viewBox="0 0 14 28"><rect x="1" y="1" width="12" height="26" rx="2" fill="none" stroke="#ea7a1c" stroke-width="1.5"/><line x1="1" y1="22" x2="13" y2="22" stroke="#ea7a1c" stroke-width="1.2"/></svg>
    <div><div class="label">CALL US ON</div><div class="value">123.555.0190</div></div>
  </div>
  <div class="abs brand">
    <div class="brand-name">tovarin</div>
    <div class="brand-tag"><i></i>BUSINESS SOLUTION LLC<i></i></div>
  </div>
  <div class="abs header-contact talk">
    <svg width="30" height="22" viewBox="0 0 30 22"><path d="M3 2h14a2 2 0 0 1 2 2v7a2 2 0 0 1-2 2H9l-5 4v-4H3a2 2 0 0 1-2-2V4a2 2 0 0 1 2-2z" fill="none" stroke="#ea7a1c" stroke-width="1.4"/><path d="M21 7h5a2 2 0 0 1 2 2v6a2 2 0 0 1-2 2h-1v3l-4-3h-6a2 2 0 0 1-2-2" fill="none" stroke="#ea7a1c" stroke-width="1.4"/></svg>
    <div><div class="label">WANT TO TALK</div><div class="value">info@tovarin.com</div></div>
  </div>
</header>

<nav class="abs main-nav">
  <a href="#">HOME</a><a href="#">WHO WE ARE</a><a href="#">WHAT WE DO</a><a href="#">WHAT MAKE US DIFFERENT</a><a href="#">WHY IT MATTERS</a><a href="#">CANDIDATE PORTAL</a><a href="#">CONTACT US</a>
</nav>

<section class="abs hero" role="img" aria-label="Photo of two businesswomen talking in a bright office, one holding a clipboard"></section>
<div class="abs hero-title">Transforming</div>
<div class="abs hero-sub">The Learning Experiance</div>
<div class="abs hero-line">Harbor Bay's Workers' Compensation<br>Attorney fighting for you!</div>
<a class="abs btn-hero quote"><span class="ic"><svg width="16" height="12" viewBox="0 0 16 12"><rect x="0.7" y="0.7" width="14.6" height="10.6" fill="none" stroke="#fff" stroke-width="1.2"/><path d="M1 1l7 6 7-6" fill="none" stroke="#fff" stroke-width="1.2"/></svg></span><span class="tx">FREE QUOTE</span></a>
<a class="abs btn-hero more"><span class="ic"><svg width="14" height="12" viewBox="0 0 14 12"><path d="M1 1l5 5-5 5M7 1l5 5-5 5" fill="none" stroke="#fff" stroke-width="1.2"/></svg></span><span class="tx">LEARN MORE</span></a>

<h1 class="abs welcome-title">WELCOME TO <span>tovarin</span></h1>
<p class="abs welcome-text"><b>Lorem Ipsum is simply dummy text of the printing and typesetting industry.</b>Lorem Ipsum has been the industry's standard dummy text ever since the 1500s, when an unknown printer took a galley of type and scrambled it to make a type specimen book. It has survived not only five centuries, but also the leap into electronic typesetting, remaining essentially unchanged.</p>

<article class="abs service" style="left:50px">
  <div class="icon"><svg width="44" height="40" viewBox="0 0 44 40" fill="#fff"><circle cx="13" cy="9" r="5"/><circle cx="29" cy="9" r="5"/><path d="M3 30c0-8 5-12 10-12s8 3 9 6"/><circle cx="24" cy="22" r="7" fill="none" stroke="#fff" stroke-width="3"/><line x1="29" y1="27" x2="38" y2="36" stroke="#fff" stroke-width="4" stroke-linecap="round"/></svg></div>
  <h3>IT Recruiting</h3>
  <p>Lorem Ipsum is simply dummy text of the printing and typesetting industry. Lorem Ipsum has been the industry's.</p>
  <span class="read">READ MORE</span>
</article>
<article class="abs service" style="left:280px">
  <div class="icon"><svg width="46" height="40" viewBox="0 0 46 40"><rect x="16" y="4" width="27" height="19" fill="none" stroke="#fff" stroke-width="2.5"/><path d="M24 23l-4 12M35 23l4 12" stroke="#fff" stroke-width="2"/><circle cx="9" cy="13" r="4" fill="#fff"/><path d="M3 36V24c0-4 3-6 6-6h4l7-5 1 2-7 7v14z" fill="#fff"/></svg></div>
  <h3>IT Training</h3>
  <p>Lorem Ipsum is simply dummy text of the printing and typesetting industry. Lorem Ipsum has been the industry's.</p>
  <span class="read">READ MORE</span>
</article>
<article class="abs service" style="left:510px">
  <div class="icon"><svg width="46" height="40" viewBox="0 0 46 40"><rect x="2" y="3" width="42" height="27" rx="2" fill="none" stroke="#fff" stroke-width="3"/><line x1="23" y1="30" x2="23" y2="37" stroke="#fff" stroke-width="2.5"/><line x1="17" y1="37" x2="29" y2="37" stroke="#fff" stroke-width="2.5"/></svg></div>
  <h3>Hardware &amp; Software Sales</h3>
  <p>Lorem Ipsum is simply dummy text of the printing and typesetting industry. Lorem Ipsum has been the industry's.</p>
  <span class="read">READ MORE</span>
</article>

<section class="abs partners"></section>
<div class="abs partners-label">
  <svg class="abs" width="136" height="101" viewBox="0 0 136 101"><polygon points="0,0 116,0 136,50 116,101 0,101" fill="#0d55a3"/></svg>
  <div class="abs txt">OUR<br>PARTNERS</div>
</div>
<div class="abs badge" style="left:212px;width:92px;background:#d3d6da"></div>
<div class="abs badge" style="left:344px;width:96px;background:#cfdccf"></div>
<div class="abs badge" style="left:467px;width:94px;background:#dcdcdc"></div>
<div class="abs badge" style="left:598px;width:92px;background:#cfd9e6"></div>

<footer>
  <div class="abs footer"></div>
  <div class="abs f-head" style="left:52px">CONTACT INFO</div>
  <div class="abs f-row" style="left:50px;top:1047px;width:170px">
    <svg width="15" height="14" viewBox="0 0 15 14" style="flex:none"><path d="M1 2l4-1 5 2 4-1v11l-4 1-5-2-4 1z M5 1v11M10 3v11" fill="none" stroke="#8a4b12" stroke-width="1"/></svg>
    <span>123 Building Name, Strret, Area, Citry, Country - Zipcode</span>
  </div>
  <div class="abs f-row" style="left:50px;top:1086px">
    <svg width="15" height="14" viewBox="0 0 15 14"><path d="M3 1l3 3-2 2c1 2 2 3 4 4l2-2 3 3-2 2C6 13 2 9 1 3z" fill="none" stroke="#8a4b12" stroke-width="1"/></svg>
    <span>01482 530617</span>
  </div>
  <div class="abs f-row" style="left:50px;top:1113px">
    <svg width="15" height="12" viewBox="0 0 15 12"><rect x="1" y="1" width="13" height="10" fill="none" stroke="#8a4b12" stroke-width="1"/><path d="M1 1l6.5 5L14 1" fill="none" stroke="#8a4b12" stroke-width="1"/></svg>
    <span>info@corvelnet.com</span>
  </div>

  <div class="abs f-head" style="left:223px">NEWS</div>
  <div class="abs news" style="left:221px;top:1046px;width:160px">
    <div class="thumb" style="background:#8a8070" role="img" aria-label="News thumbnail photo"></div>
    <div>Lorem Ipsum is simply dummy text of the printing<small>Today 5:60 pm - 12.06.2016</small></div>
  </div>
  <div class="abs news" style="left:221px;top:1094px;width:160px">
    <div class="thumb" style="background:#8f6b55" role="img" aria-label="News thumbnail photo"></div>
    <div>Lorem Ipsum is simply dummy text of the printing<small>Today 2:10 pm - 12.06.2016</small></div>
  </div>

  <div class="abs f-head" style="left:394px">TESTIMONIALS</div>
  <div class="abs arrow-box" style="left:524px"><svg width="6" height="8"><path d="M5 0L1 4l4 4" fill="none" stroke="#8a4b12"/></svg></div>
  <div class="abs arrow-box" style="left:541px;background:#8a4b12"><svg width="6" height="8"><path d="M1 0l4 4-4 4" fill="none" stroke="#fff"/></svg></div>
  <div class="abs" style="left:393px;top:1047px;width:41px;height:41px;border-radius:50%;background:#5a5550" role="img" aria-label="Portrait of the client giving the testimonial"></div>
  <div class="abs" style="left:443px;top:1051px;font-size:11px;color:var(--blue)">Marek Oblonsky</div>
  <div class="abs" style="left:443px;top:1067px;font-size:9.5px;font-style:italic;color:#6b3e10">CEO</div>
  <div class="abs" style="left:393px;top:1094px;width:170px;font-size:9.2px;line-height:14px;color:#6b3e10">"Lorem Ipsum is simply dummy text of the printing and typesetting industry. Lorem Ipsum has been the industry."</div>

  <div class="abs foot-brand"><div class="n">tovarin</div><div class="t">BUSINESS SOLUTION LLC</div></div>
  <div class="abs social" style="left:599px;background:var(--orange-icon)"></div>
  <div class="abs social" style="left:632px;border:1.5px solid #fff"></div>
  <div class="abs social" style="left:663px;border:1.5px solid #fff"></div>

  <div class="abs copyright">@ Tovarin Business Solutions LLC - 2016. All Rights Reserved.</div>
</footer>

</body>
</html>
```